Chimney Service company needs new business card design

We need a updated business card with our new logo added. We provide a full range of chimney services throughout Vermont and New Hampshire. The business card will be one sided and color. Attached is our current business card another document showing all the information we would like on the card.
We dont like a lot of flashy colors.... here is a link to our website to get an idea of our branding www.flueguardianvt.example

Target Market(s)

homeowners

Industry/Entity Type

Business

Contact Information for Business Card

See attached sheet for content.

Font styles to use
Serif
Sans Serif

Requirements
Must have
• all information provided on separate sheet
Should not have
• Additional information that may clogg up design

```html
<!DOCTYPE html>
<html lang="en">
<head>
<meta charset="utf-8">
<title>Flue Guardian – Business Card</title>
<link rel="stylesheet" href="https://fonts.googleapis.com/css2?family=Cinzel:wght@500&family=Open+Sans:wght@400;600;700&display=swap">
<style>
  :root {
    --backdrop: #b9b9b9;
    --charcoal: #2e2e2e;
    --charcoal-dark: #262626;
    --paper: #f1f1f1;
    --paper-edge: #e4e4e4;
    --ember: #8e0c10;
    --ember-light: #a8161b;
    --ink: #2b2b2b;
    --white: #f4f4f4;
  }
  * { box-sizing: border-box; margin: 0; padding: 0; }
  html, body {
    width: 1200px; height: 576px; overflow: hidden;
    background: var(--backdrop);
    font-family: "Open Sans", Arial, sans-serif;
  }
  .canvas { position: relative; width: 1200px; height: 576px; }

  .card {
    position: absolute; top: 138px;
    width: 484px; height: 292px;
    border-radius: 13px; overflow: hidden;
    box-shadow: 0 4px 8px rgba(0,0,0,.25);
  }

  /* Front */
  .card-front { left: 82px; background: var(--charcoal); }
  .brand {
    position: absolute; left: 0; right: 0; top: 86px;
    display: flex; flex-direction: column; align-items: center;
  }
  .brand-mark {
    width: 40px; height: 40px;
    border: 5px solid var(--white);
    margin-bottom: 18px;
  }
  .brand-name {
    font-family: "Cinzel", Georgia, serif;
    font-weight: 500; font-size: 27px; letter-spacing: 1px;
    color: var(--white); line-height: 1;
  }
  .brand-since {
    display: flex; align-items: center; gap: 8px; margin-top: 4px;
    font-family: "Cinzel", Georgia, serif;
    font-weight: 500; font-size: 13px; letter-spacing: 1px;
    color: var(--white);
  }
  .brand-since::before, .brand-since::after {
    content: ""; width: 90px; height: 1.5px; background: var(--white);
  }

  /* Back */
  .card-back {
    left: 602px;
    background: linear-gradient(180deg, var(--paper) 0%, var(--paper-edge) 100%);
  }
  .services {
    position: absolute; left: 24px; top: 26px; list-style: none;
    font-size: 14px; line-height: 18.7px; color: var(--ink);
  }
  .services li { display: flex; align-items: center; gap: 10px; }
  .services li::before {
    content: ""; width: 6px; height: 8px;
    border-radius: 3px 3px 1px 1px; background: var(--ember);
  }
  .coverage {
    position: absolute; left: 23px; top: 150px; width: 232px;
  }
  .coverage-title {
    font-weight: 700; font-size: 14.5px; line-height: 20px;
    color: var(--ember); white-space: nowrap;
  }
  .coverage-since {
    display: flex; align-items: center; gap: 6px; margin: 1px 8px 0 0;
    font-size: 9.5px; line-height: 12px; letter-spacing: .5px; color: var(--ink);
    white-space: nowrap;
  }
  .coverage-since::before, .coverage-since::after {
    content: ""; flex: 1; height: 1.5px; background: var(--ember);
  }
  .contact {
    position: absolute; left: 24px; top: 197px; list-style: none;
    font-size: 12.5px; line-height: 19px; color: var(--ink);
  }
  .contact li { display: flex; align-items: center; gap: 14px; white-space: nowrap; }
  .contact svg { width: 11px; height: 11px; fill: var(--ember); flex: none; }
  .contact .domain { color: var(--ember); }

  .flame-art {
    position: absolute; left: 298px; top: 42px; width: 160px; height: 228px;
    border-radius: 50% 50% 40% 40% / 70% 70% 30% 30%;
    background: linear-gradient(180deg, var(--ember-light), var(--ember));
  }

  .strip-insured {
    position: absolute; left: 0; top: 266px; width: 264px; height: 26px;
    background: var(--ember); border-top-right-radius: 4px;
    color: var(--white); font-size: 11.5px; line-height: 26px; padding-left: 24px;
  }
  .strip-family {
    position: absolute; left: 270px; top: 253px; width: 214px; height: 39px;
    background: var(--charcoal-dark); border-top-left-radius: 4px;
    color: var(--white); font-size: 11.5px; line-height: 39px; text-align: center;
  }
</style>
</head>
<body>
<main class="canvas">

  <section class="card card-front" aria-label="Card front">
    <div class="brand">
      <div class="brand-mark"></div>
      <div class="brand-name">FLUE GUARDIAN</div>
      <div class="brand-since">INC 1989</div>
    </div>
  </section>

  <section class="card card-back" aria-label="Card back">
    <ul class="services">
      <li>Full Masonry Services</li>
      <li>Historic chimney restoration</li>
      <li>Stainless steel liners</li>
      <li>New Chimney installations</li>
      <li>FSCA Certified Chimney sweeps</li>
    </ul>

    <div class="coverage">
      <div class="coverage-title">Serving VT and New Hampshire</div>
      <div class="coverage-since">SINCE 1989</div>
    </div>

    <ul class="contact">
      <li>
        <svg viewBox="0 0 12 12" aria-hidden="true"><path d="M1 3c0-1 1-2 5-2s5 1 5 2v1H8V3H4v1H1zM2 5h8l1 6H1z"/></svg>
        802-555-0147
      </li>
      <li>
        <svg viewBox="0 0 12 12" aria-hidden="true"><path d="M0 2h12v8H0zM1 3l5 4 5-4v-.2H1z" fill-rule="evenodd"/></svg>
        info@flueguardianvt.example
      </li>
      <li>
        <svg viewBox="0 0 12 12" aria-hidden="true"><circle cx="6" cy="6" r="5.5"/><path d="M0.5 6h11M6 .5v11" stroke="#f1f1f1" stroke-width="1"/></svg>
        <span>www.<span class="domain">flueguardianvt</span>.example</span>
      </li>
    </ul>

    <div class="flame-art" role="img" aria-label="Large red flame decoration"></div>

    <div class="strip-insured">Fully Insured – Free Estimates</div>
    <div class="strip-family">Family Owned &amp; Operated</div>
  </section>

</main>
</body>
</html>
```